American cannabis tech company business card design

Pavrel.com is seeking a modern, professional, and brand-aligned business card that represents our company and its core values: Mission, Story, Values, and Impact. As an innovative cannabis company, we want a business card that is not only visually appealing but also serves as a representation of who we are and what we stand for.

Project Scope: Design a double-sided business card that integrates our brand identity and core values. Incorporate our key brand elements, ensuring a sleek and contemporary aesthetic. Visually reflect our core values (Mission, Story, Values, Impact) in a way that is engaging yet professional.

Target Market(s)

Vendors, third parties,

Contact Information for Business Card

Contact details (name, title, email, phone, website, etc.)

Font styles to use
Other font styles liked:
• Caslon, Centra

Colors

Designer to choose colors to be used in the design.

Requirements
Must have
• Pavrel.com logo and branding A creative yet clean way to integrate our core values (Mission, Story, Values, Impact) Modern typography and a well-structured layout
Nice to have
• forest green, grey, white, black
Should not have
• references to marijuana, leafs, plants, or related product

```html
<!DOCTYPE html>
<html lang="en">
<head>
<meta charset="utf-8">
<title>Pavrel.com — Business Card</title>
<link rel="stylesheet" href="https://fonts.googleapis.com/css2?family=Libre+Caslon+Text:wght@700&family=Montserrat:wght@400;500&display=swap">
<style>
  :root {
    --forest: #1c3320;
    --forest-soft: #27402a;
    --paper: #ffffff;
    --cream: #faf8f1;
    --ink: #1a1a1a;
    --backdrop: #2a2a2a;
  }
  * { margin: 0; padding: 0; box-sizing: border-box; }
  html, body { width: 1200px; height: 1015px; overflow: hidden; }
  body {
    background: var(--backdrop);
    display: flex;
    flex-direction: column;
    align-items: center;
    justify-content: center;
    gap: 56px;
  }
  .card {
    width: 700px;
    height: 400px;
    position: relative;
    overflow: hidden;
    box-shadow: 0 10px 30px rgba(0,0,0,.45);
  }
  .wordmark {
    font-family: "Libre Caslon Text", Georgia, serif;
    font-weight: 700;
    color: var(--cream);
    letter-spacing: 2px;
    line-height: 1;
  }
  .card-front {
    background: var(--forest);
    display: flex;
    align-items: center;
    justify-content: center;
  }
  .card-front .wordmark { font-size: 104px; }

  .card-back { display: flex; background: var(--paper); }
  .contact-panel {
    width: 44%;
    padding: 40px 34px;
    display: flex;
    flex-direction: column;
    justify-content: space-between;
    color: var(--ink);
  }
  .person-name {
    font-family: "Libre Caslon Text", Georgia, serif;
    font-weight: 700;
    font-size: 24px;
    color: var(--forest);
  }
  .person-title {
    font-family: "Libre Caslon Text", Georgia, serif;
    font-weight: 700;
    font-size: 11px;
    margin-top: 4px;
    padding-left: 14px;
  }
  .address {
    font-family: "Montserrat", Arial, sans-serif;
    font-size: 15px;
    line-height: 1.25;
    margin-bottom: 16px;
  }
  .contact-list { list-style: none; font-family: "Montserrat", Arial, sans-serif; font-size: 15px; }
  .contact-list li { display: flex; align-items: center; gap: 10px; line-height: 1.55; }
  .contact-list svg { width: 14px; height: 14px; fill: var(--forest); flex: none; }
  .brand-panel {
    flex: 1;
    background: var(--forest-soft);
    display: flex;
    align-items: center;
    justify-content: center;
  }
  .brand-panel .wordmark { font-size: 62px; }
</style>
</head>
<body>
  <section class="card card-front" aria-label="Card front">
    <span class="wordmark">PAVREL</span>
  </section>

  <section class="card card-back" aria-label="Card back">
    <div class="contact-panel">
      <div class="person">
        <h1 class="person-name">Dana Whitfield</h1>
        <p class="person-title">Owner</p>
      </div>
      <div class="details">
        <p class="address">418 Linden Grove Ave, #112<br>Brookhaven, OH 43990</p>
        <ul class="contact-list">
          <li><svg viewBox="0 0 24 24"><path d="M6.6 10.8a15.1 15.1 0 0 0 6.6 6.6l2.2-2.2c.3-.3.7-.4 1-.2 1.1.4 2.3.6 3.6.6.6 0 1 .4 1 1V20c0 .6-.4 1-1 1A17 17 0 0 1 3 4c0-.6.4-1 1-1h3.5c.6 0 1 .4 1 1 0 1.3.2 2.5.6 3.6.1.3 0 .7-.2 1z"/></svg>555-014-2237</li>
          <li><svg viewBox="0 0 24 24"><path d="M2 5h20v14H2z M2 5l10 8 10-8" /></svg>info@pavrel.com</li>
          <li><svg viewBox="0 0 24 24"><circle cx="12" cy="12" r="10"/></svg>www.pavrel.com</li>
        </ul>
      </div>
    </div>
    <div class="brand-panel">
      <span class="wordmark">PAVREL</span>
    </div>
  </section>
</body>
</html>
```